BRTL web site redesign

Coastal Linkage Engineering service (BRTL) is a diverse technology company specialising in design and installation of fibre optics, network convergence and building services, for commercial clients in Australia, we required a new design of our website to attract new clients, generate sales leads, and provide information about our services to the market. The site and should have a new technology look and feel and be designed in word press. our branding colour is blue.

Target Market(s)

New developments, Construction organisations, Commercial end users, IT managers, Consultants.

Industry/Entity Type

It Company

Number of Pages Required

5+ page

Font styles to use
Sans Serif

Colors
0292cd
3176b5

Requirements
Must have
• key pages.
• Home page with some sizzle, automated pictures running through, I like the look of this competitor website http://www.gleamwirex.com.au/ good clean menus and easy to navigate.
• Services page our key services are Fibre optics, Security, Building services,Electrical. I would like the same page layout (Design) for all our services, with a find out more link on each page, manly picture driven with text around our key messaging.
• About us page with space for company profile and directors pictures, bio and contact information.
• Certifications / Accreditations page with have over 20 certifications on different products from suppliers, and a number of licences from governing bodies.
• Current and past projects page with case studies and customer outcomes
• Contact us page with options around what services they require more information on, please keep in mind the site is around generating sales Leeds and being seen as an industry expert.
Nice to have
• RSS feeds, Linked in link, to be placed within the design, Consistent BRTL branding,Same colour blue as our logo Document library for education information, white papers, presentations etc,
• a new technology look and feel, mobile friendly.
Should not have
• boring layout, move away from our cuurent website http://www.brtlgroup.com.au/
• no e eCommerce store required.

```html
<!DOCTYPE html>
<html lang="en">
<head>
<meta charset="utf-8">
<title>BRTL – Coastal Linkage Engineering service</title>
<link href="https://fonts.googleapis.com/css2?family=Arimo:wght@400;700&display=swap" rel="stylesheet">
<style>
:root{
  --blue:#0292cd;
  --blue-dark:#3176b5;
  --ink:#222;
  --text:#555;
  --muted:#888;
  --line:#ddd;
  --panel:#f2f2f2;
  --footer:#2e2e2e;
  --footer-deep:#1f1f1f;
  --red:#d9261c;
  --orange:#e58a00;
}
*{box-sizing:border-box;margin:0;padding:0}
html,body{width:1200px;height:2706px;overflow:hidden;background:#fff}
body{font-family:"Arimo",Arial,sans-serif;color:var(--text);font-size:12px;line-height:1.45;position:relative}
.wrap{width:840px;margin:0 auto;position:relative}
a{color:inherit;text-decoration:none}

/* header */
.site-header{height:132px;position:relative}
.brand{position:absolute;left:180px;top:32px;display:flex;align-items:center;gap:10px}
.brand-mark{width:22px;height:22px;background:var(--blue)}
.brand-name{font-size:40px;font-weight:700;color:var(--blue);letter-spacing:1px}
.brand-sub{position:absolute;left:180px;top:82px;font-size:9px;color:var(--blue);text-transform:uppercase;width:220px}
.account-bar{position:absolute;left:780px;top:0;width:240px;height:24px;background:#222;color:#fff;font-size:10px;display:flex;justify-content:space-around;align-items:center;text-transform:uppercase}
.phone{position:absolute;left:555px;top:76px;display:flex;align-items:center;gap:10px;font-size:26px;font-weight:700;color:#333}
.search{position:absolute;left:805px;top:82px;display:flex}
.search-field{width:140px;height:22px;border:1px solid #ccc;font-size:10px;color:#999;padding:4px}
.search-btn{width:55px;height:22px;background:var(--blue);color:#fff;font-size:10px;text-align:center;line-height:22px}
.main-nav{position:absolute;left:355px;top:134px;display:flex;gap:26px;font-size:13px;color:#333;text-transform:uppercase}
.main-nav .active{color:var(--blue)}

/* hero */
.hero{position:absolute;top:162px;left:0;width:1200px;height:365px;background:linear-gradient(120deg,#3a4a55 0%,#6c7f8c 35%,#2f6d9a 60%,#1c2c38 100%)}
.hero-caption{position:absolute;left:0;top:230px;width:1200px;height:70px;background:rgba(0,0,0,.55);padding:10px 0 0 215px;color:#fff}
.hero-caption h1{font-size:24px;text-transform:uppercase;font-weight:700}
.hero-caption p{font-size:13px;margin-top:4px}
.hero-dots{position:absolute;left:585px;top:335px;display:flex;gap:6px}
.hero-dots i{width:12px;height:12px;background:#fff;opacity:.6}
.hero-dots i:first-child{opacity:1;background:var(--blue)}

/* intro columns */
.intro{position:absolute;top:568px;left:180px;width:840px;display:flex;justify-content:space-between}
.intro-col{width:250px;text-align:left}
.intro-col h2{font-size:14px;color:var(--blue);text-transform:uppercase;display:flex;align-items:center;gap:10px;margin-bottom:14px;padding-left:40px;font-weight:400}
.intro-col p{font-size:11px;padding-left:40px;height:120px}
.intro-col ul{list-style:none;font-size:12px;height:120px}
.intro-col li{border-bottom:1px solid var(--line);padding:6px 0}
.btn{display:inline-block;background:var(--blue);color:#fff;font-size:10px;padding:6px 14px}
.intro-col .btn{margin-left:100px;margin-top:14px}

/* welcome */
.welcome{position:absolute;top:860px;left:180px;width:840px;border-top:1px solid var(--line);padding-top:10px}
.welcome h2{font-size:24px;color:#333;font-weight:400}
.welcome h2 span{color:var(--blue)}
.welcome p{width:540px;font-size:11px;margin-top:10px}
.welcome .more{position:absolute;left:500px;top:140px;color:var(--orange);font-size:10px}
.welcome-photo{position:absolute;right:0;top:8px;width:260px;height:160px;background:linear-gradient(135deg,#cfd8e0,#8aa3b6 60%,#5a7182)}

/* tabs */
.showcase{position:absolute;top:1050px;left:180px;width:840px;height:175px;background:var(--panel)}
.tabs{display:flex}
.tabs span{width:150px;height:38px;line-height:38px;text-align:center;font-size:12px;background:#e2e2e2;color:#444;text-transform:uppercase;border-right:1px solid #ccc}
.tabs .current{background:var(--blue);color:#fff}
.thumbs{display:flex;justify-content:center;gap:28px;margin-top:30px}
.thumb{width:90px;height:70px;border:4px solid #fff;box-shadow:0 0 0 1px #ddd}

/* about + form */
.about{position:absolute;top:1228px;left:180px;width:420px;text-align:right}
.about h2{font-size:24px;color:#222;text-align:center;font-weight:400;margin-bottom:16px;padding-left:140px}
.about p{font-size:11px;margin:0 0 14px auto;width:300px}
.about .btn{position:absolute;left:150px;top:425px}
.quick{position:absolute;top:1218px;left:630px;width:390px;height:455px;background:var(--panel);padding:20px 26px}
.quick h2{font-size:22px;color:var(--blue);text-align:center;font-weight:400;margin-bottom:24px;text-transform:uppercase}
.field{display:flex;align-items:flex-start;margin-bottom:14px;font-size:11px;color:#333}
.field label{width:80px;padding-top:6px}
.field .box{flex:1;height:28px;background:#fff;border:1px solid #ccc}
.field .area{height:125px}
.quick .btn{margin-left:80px;width:250px;text-align:center;padding:9px 0;margin-top:10px}

/* partners */
.partners{position:absolute;top:1710px;left:180px;width:840px;text-align:center;border-top:1px solid var(--line);padding-top:12px}
.partners h2{font-size:24px;color:#222;font-weight:700}
.partners p{font-size:11px;margin-top:8px}
.partner-row{display:flex;justify-content:space-between;margin-top:46px;padding:0 25px}
.partner-badge{width:130px;height:44px;background:#c9c9c9;border-radius:4px}

/* testimonials */
.testimonials{position:absolute;top:1965px;left:180px;width:840px;border-top:1px solid var(--line);padding-top:12px}
.testimonials h2{font-size:24px;color:#222;margin-bottom:22px}
.quotes{display:grid;grid-template-columns:1fr 1fr;gap:26px 60px}
.quote{display:flex;gap:16px}
.avatar{width:54px;height:54px;border-radius:50%;background:linear-gradient(135deg,#d7c3b0,#8d7766);flex:none}
.quote p{font-size:10px;width:280px}
.quote .who{font-size:10px;margin-top:10px;color:#333}
.quote .who b{color:var(--red);font-weight:400}

/* footer */
.site-footer{position:absolute;top:2296px;left:0;width:1200px;height:410px;background:var(--footer);color:#ccc}
.footer-cols{position:absolute;left:180px;top:12px;width:840px;display:flex;justify-content:space-between}
.footer-cols h3{font-size:11px;color:#fff;text-transform:uppercase;font-weight:400;margin-bottom:8px}
.footer-cols ul{list-style:none;font-size:11px;line-height:21px}
.news li{display:flex;gap:8px;margin-bottom:8px;line-height:13px;font-size:10px;width:230px}
.news i{width:40px;height:28px;background:#5d7080;flex:none}
.view-all{position:absolute;left:0;width:1200px;top:198px;text-align:center;font-size:11px;color:#fff}
.newsletter{position:absolute;left:0;top:220px;width:1200px;height:150px;background:var(--footer-deep);text-align:center;padding-top:10px}
.newsletter p{font-size:11px;color:#ddd;width:260px;margin:0 auto}
.signup{display:flex;justify-content:center;align-items:center;gap:10px;margin-top:12px}
.signup h3{font-size:20px;color:#fff;font-weight:400;text-transform:uppercase}
.signup .input{width:230px;height:26px;background:#fff;color:#999;font-size:11px;text-align:left;padding:6px}
.signup .btn{padding:7px 16px;font-size:12px}
.follow{display:flex;justify-content:center;align-items:center;gap:6px;margin-top:14px;font-size:10px;color:#ddd;text-transform:uppercase}
.follow i{width:18px;height:18px;background:var(--blue-dark)}
.copyright{position:absolute;left:0;bottom:0;width:1200px;height:32px;line-height:32px;text-align:center;font-size:11px;background:#151515;color:#ccc}
</style>
</head>
<body>

<header class="site-header">
  <div class="brand"><span class="brand-mark"></span><span class="brand-name">BRTL</span></div>
  <div class="brand-sub">Coastal Linkage Engineering service</div>
  <div class="account-bar"><span>My Account</span><span>My Cart</span></div>
  <div class="phone">
    <svg width="22" height="26" viewBox="0 0 22 26"><path d="M5 1c2 0 3 5 3 6s-3 2-3 3c0 3 4 8 7 9 1 0 2-3 3-3s6 2 6 4c0 2-3 5-5 5C8 25 1 16 1 6 1 3 3 1 5 1z" fill="#333"/></svg>
    1300 555 014
  </div>
  <div class="search"><div class="search-field">Keywords</div><div class="search-btn">Search</div></div>
  <nav class="main-nav">
    <a class="active">Home</a><a>About Us</a><a>Services</a><a>ISP</a><a>Recent Projects</a><a>Blog</a><a>Contact Us</a>
  </nav>
</header>

<section class="hero" role="img" aria-label="Slideshow photo of fibre optic cabling and network equipment">
  <div class="hero-caption">
    <h1>Lorm ipsum dolor sit amet, consectetur adipiscing</h1>
    <p>Lorem ipsum dolor sit amet, consectetur adipiscing elit. Sed diam nonumy eirmod tempor invidunt.</p>
  </div>
  <div class="hero-dots"><i></i><i></i><i></i><i></i></div>
</section>

<section class="intro">
  <div class="intro-col">
    <h2><svg width="26" height="18" viewBox="0 0 26 18"><circle cx="7" cy="5" r="4" fill="#0292cd"/><circle cx="19" cy="5" r="4" fill="#0292cd"/><path d="M0 18c0-6 14-6 14 0zM12 18c0-6 14-6 14 0z" fill="#0292cd"/></svg>Who we are</h2>
    <p>Lorem ipsum dolor sit amet, consectetur adipiscing elit. Sed diam nonumy in convallis gravida neque. Nulla gravida eros tincidunt mattis a accumsan, aliquam in sagit fis ut. Sollicitudin sed massa sit amet, curabitur tempus semper vel sed lobortis volutpat mattis sed enim.</p>
    <a class="btn">Read more</a>
  </div>
  <div class="intro-col">
    <h2><svg width="18" height="22" viewBox="0 0 18 22"><rect x="1" y="1" width="16" height="20" fill="none" stroke="#0292cd" stroke-width="2"/><path d="M4 7h10M4 11h10M4 15h7" stroke="#0292cd" stroke-width="2"/></svg>What we do</h2>
    <p>Lorem ipsum dolor sit amet, consectetur adipiscing elit. Sed diam nonumy in convallis gravida neque. Nulla gravida eros tincidunt mattis a accumsan, aliquam in sagit fis ut. Sollicitudin sed massa sit amet, curabitur tempus semper vel sed lobortis volutpat mattis sed enim.</p>
    <a class="btn">Read more</a>
  </div>
  <div class="intro-col">
    <h2 style="padding-left:0"><svg width="22" height="22" viewBox="0 0 22 22"><circle cx="11" cy="11" r="5" fill="none" stroke="#0292cd" stroke-width="3"/><path d="M11 0v5M11 17v5M0 11h5M17 11h5M3 3l4 4M15 15l4 4M19 3l-4 4M3 19l4-4" stroke="#0292cd" stroke-width="3"/></svg>Our services</h2>
    <ul>
      <li>Commercial Security Systems</li>
      <li>Data &amp; Fibre Installations</li>
      <li>Information Communication &amp; Technology</li>
      <li>Electrical Fit Out</li>
    </ul>
    <a class="btn" style="margin-left:60px">Read more</a>
  </div>
</section>

<section class="welcome">
  <h2>Wecome to <span>BRTL.com</span></h2>
  <p>Lorem ipsum dolor sit amet, consectetur adipiscing elit. Sed diam nonumy in convallis gravida neque. Nulla gravida vestibulum mattis a accumsan, aliquam in sagittis ut. Sollicitudin sed massa sit amet venenatis. Curabitur tempus semper vel vestibulum volutpat mattis sed ullamcorper nisl. Sed aliquam dolor sit amet consequat gravida. Fusce tempus tempor leo feugiat vel amet. Tincidunt quis nunc lorem semper ornare amet. Lorem ipsum dolor sit amet, consectetur adipiscing elit.</p>
  <a class="more">Read more</a>
  <div class="welcome-photo" role="img" aria-label="Photo of a business professional in a suit using a tablet"></div>
</section>

<section class="showcase">
  <div class="tabs"><span class="current">Featured</span><span>New Arrivals</span><span>On Sale</span></div>
  <div class="thumbs">
    <div class="thumb" role="img" aria-label="Project photo of a server room" style="background:linear-gradient(135deg,#9fb8cc,#4d6d88)"></div>
    <div class="thumb" role="img" aria-label="Project photo of cabling work" style="background:linear-gradient(135deg,#c7b39a,#6a7f91)"></div>
    <div class="thumb" role="img" aria-label="Project photo of network hardware" style="background:linear-gradient(135deg,#1d3c6a,#3176b5)"></div>
    <div class="thumb" role="img" aria-label="Project photo of fibre optic strands" style="background:linear-gradient(135deg,#7fc4e6,#0292cd)"></div>
    <div class="thumb" role="img" aria-label="Project photo of a technician at work" style="background:linear-gradient(135deg,#dfe6ec,#6e879a)"></div>
  </div>
</section>

<section class="about">
  <h2>ABOUT US</h2>
  <p>Lorem ipsum dolor sit amet, consectetur adipiscing elit. Sed diam nonumy in convallis gravida neque. Nulla gravida vestibulum mattis a accumsan, aliquam in sagittis ut. Sollicitudin sed massa sit amet venenatis. Curabitur tempus semper vel vestibulum volutpat mattis sed enim.</p>
  <p>Lorem ipsum dolor sit amet consectetur adipiscing elit, sed diam nonumy eirmod tempor invidunt ut labore. Nulla gravida vestibulum mattis a accumsan aliquam in sagittis ut. Sollicitudin sed massa ut enim venenatis, curabitur tempus sem per vel sed lobortis volutpat mattis sed ullamcorper nisl vestibulum.</p>
  <a class="btn">Read more</a>
</section>

<section class="quick">
  <h2>Quick Question</h2>
  <div class="field"><label>Name</label><div class="box"></div></div>
  <div class="field"><label>Phone</label><div class="box"></div></div>
  <div class="field"><label>Email</label><div class="box"></div></div>
  <div class="field"><label>Message</label><div class="box area"></div></div>
  <a class="btn">SUBMIT</a>
</section>

<section class="partners">
  <h2>Our Partners</h2>
  <p>Lorem ipsum dolor sit amet, consectetur adipiscing elit. Sed diam nonumy fermentum gravida neque.</p>
  <div class="partner-row">
    <div class="partner-badge"></div><div class="partner-badge"></div><div class="partner-badge"></div><div class="partner-badge"></div><div class="partner-badge"></div>
  </div>
</section>

<section class="testimonials">
  <h2>What Our Customer Says</h2>
  <div class="quotes">
    <div class="quote"><div class="avatar" role="img" aria-label="Customer portrait"></div><div><p>Lorem ipsum dolor sit amet, consectetur adipiscing elit. Sed diam nonumy fermentum gravida neque. Nulla gravida vestibulum mattis a accumsan aliquam.</p><div class="who"><b>Mara Ellison</b>, Marketing, Perth</div></div></div>
    <div class="quote"><div class="avatar" role="img" aria-label="Customer portrait"></div><div><p>Lorem ipsum dolor sit amet, consectetur adipiscing elit. Sed diam nonumy fermentum gravida neque. Nulla gravida vestibulum mattis a accumsan aliquam.</p><div class="who"><b>Dev Kapoor</b>, IT Engineer, Washington</div></div></div>
    <div class="quote"><div class="avatar" role="img" aria-label="Customer portrait"></div><div><p>Lorem ipsum dolor sit amet, consectetur adipiscing elit. Sed diam nonumy fermentum gravida neque. Nulla gravida vestibulum mattis a accumsan aliquam.</p><div class="who"><b>Tom Halvers</b>, Public Relations, New York</div></div></div>
    <div class="quote"><div class="avatar" role="img" aria-label="Customer portrait"></div><div><p>Lorem ipsum dolor sit amet, consectetur adipiscing elit. Sed diam nonumy fermentum gravida neque. Nulla gravida vestibulum mattis a accumsan aliquam.</p><div class="who"><b>Rina Castell</b>, CEO, Marketing, Adelaide</div></div></div>
  </div>
</section>

<footer class="site-footer">
  <div class="footer-cols">
    <div><h3>Main Menu</h3><ul><li>Home</li><li>About Us</li><li>Services</li><li>ISP</li><li>Recent Projects</li><li>Blog</li><li>Contact Us</li></ul></div>
    <div><h3>Latest News &amp; Updates</h3><ul class="news">
      <li><i></i>January, 13th 2016 Lorem ipsum dolor sit amet consectetur</li>
      <li><i></i>February, 07th 2016 Lorem ipsum dolor sit amet consectetur</li>
      <li><i></i>March, 11th 2016 Lorem ipsum dolor sit amet consectetur</li>
      <li><i></i>March, 24th 2016 Lorem ipsum dolor sit amet consectetur</li>
    </ul></div>
    <div><h3>Useful Links</h3><ul><li>Terms &amp; Conditions</li><li>Privacy policy</li><li>HELP</li><li>FAQs</li><li>Sitemap</li></ul></div>
    <div><h3>My Account</h3><ul><li>My Account</li><li>Sign In</li><li>Order Status</li><li>My Cart</li><li>My WhishList</li></ul></div>
  </div>
  <div class="view-all">View All</div>
  <div class="newsletter">
    <p>Receive Our News &amp; updates weekly, no worry about your details</p>
    <div class="signup"><h3>Newsletter</h3><div class="input">Your email address</div><a class="btn">SUBMIT</a></div>
    <div class="follow">Follow us on <i></i><i></i><i></i><i></i><i></i><i></i></div>
  </div>
  <div class="copyright">Copyright © 2016 BRTL.com. All right reserved.</div>
</footer>

</body>
</html>
```